U.S. Popcorn company needs business cards

We are a popcorn company that manufactures popcorn and sells it to grocery stores worldwide. Our theme is "Americana" and our logo is U.S. route 66 which is the most famous highway in the U.S.

We would like the design to be simple and to use both sides. On the back side we would like to see just the logo and website. The front would be normal details

Target Market(s)

Wholesalers, grocers and distributors

Industry/Entity Type

Manufacture

Contact Information for Business Card

Business name: Prairie Lantern Popcorn
Phone: +1 555 308 4726
Email: Dale@prairielanternpopcorn.com
website: www.prairielanternpopcorn.com
Tag Line: "Fresh from the kettle"
Name: Dale Whitcombe
Title: Founder/President

Requirements
Must have
• Either this design should be fun or clean and simple. I will let you show me your thougths.
Nice to have
• Anything that ties in the real Hwy Route 66.
• Colors might need to be red, white and blue incorporated.
Should not have
• Not be too busy.

```html
<!DOCTYPE html>
<html lang="en">
<head>
<meta charset="utf-8">
<title>Prairie Lantern Popcorn – Business Cards</title>
<link rel="stylesheet" href="https://fonts.googleapis.com/css2?family=Lato:wght@400;700&family=Raleway:wght@700&display=swap">
<style>
  :root {
    --navy: #0d2a6b;
    --red: #e31b23;
    --ink: #1c1c1c;
    --paper: #ffffff;
    --backdrop: #eeeeee;
    --edge: #dcdcdc;
  }
  * { box-sizing: border-box; margin: 0; padding: 0; }
  html, body {
    width: 1200px; height: 586px; overflow: hidden;
    background: var(--backdrop);
  }
  .canvas { position: relative; width: 1200px; height: 586px; }

  .card {
    position: absolute; top: 128px;
    width: 502px; height: 302px;
    background: var(--paper);
    border: 1px solid var(--edge);
    overflow: hidden;
  }
  .card--back { left: 61px; }
  .card--front { left: 619px; }

  .brand {
    position: absolute;
    display: flex; align-items: center; gap: 10px;
    font-family: "Lato", sans-serif; font-weight: 700;
    color: var(--navy);
    line-height: 1.15;
  }
  .brand__dot { flex: none; border-radius: 50%; background: var(--red); }

  .card--back .brand {
    left: 0; right: 0; top: 84px; justify-content: center;
    font-size: 30px;
  }
  .card--back .brand__dot { width: 34px; height: 34px; }
  .card--back .brand__name { width: 220px; }

  .tagline {
    position: absolute; left: 0; right: 0; top: 260px;
    text-align: center;
    font-family: "Lato", sans-serif; font-weight: 400;
    font-size: 12px; letter-spacing: 2px; color: var(--ink);
  }

  .card--front .brand {
    left: 30px; top: 122px; width: 200px;
    font-size: 22px;
  }
  .card--front .brand__dot { width: 26px; height: 26px; }

  .divider {
    position: absolute; left: 252px; top: 72px;
    width: 2px; height: 156px;
    background: linear-gradient(to bottom, transparent, var(--navy) 30%, var(--navy) 70%, transparent);
  }

  .person { position: absolute; left: 281px; top: 82px; }
  .person__name {
    font-family: "Raleway", sans-serif; font-weight: 700;
    font-size: 17px; line-height: 22px; color: var(--red);
  }
  .person__title {
    font-family: "Lato", sans-serif; font-weight: 400;
    font-size: 12px; line-height: 16px; color: var(--ink);
    margin-top: 2px;
  }

  .contact {
    position: absolute; left: 281px; top: 158px;
    list-style: none;
    font-family: "Lato", sans-serif; font-weight: 700;
    font-size: 12px; color: var(--ink);
  }
  .contact__item { display: flex; align-items: center; gap: 9px; height: 18px; margin-bottom: 6px; white-space: nowrap; }
  .contact__icon { width: 13px; height: 13px; fill: var(--navy); flex: none; }

  .web-band {
    position: absolute; left: 0; right: 0; bottom: 0; height: 27px;
    background: var(--navy);
    display: flex; align-items: center; justify-content: center;
    font-family: "Lato", sans-serif; font-weight: 700;
    font-size: 11px; letter-spacing: 2.4px; color: var(--paper);
  }
</style>
</head>
<body>
<main class="canvas">

  <section class="card card--back" aria-label="Card back">
    <div class="brand">
      <span class="brand__dot"></span>
      <span class="brand__name">Prairie Lantern Popcorn</span>
    </div>
    <p class="tagline">Fresh from the kettle</p>
  </section>

  <section class="card card--front" aria-label="Card front">
    <div class="brand">
      <span class="brand__dot"></span>
      <span class="brand__name">Prairie Lantern Popcorn</span>
    </div>

    <div class="divider"></div>

    <div class="person">
      <h1 class="person__name">Dale Whitcombe</h1>
      <p class="person__title">Founder/President</p>
    </div>

    <ul class="contact">
      <li class="contact__item">
        <svg class="contact__icon" viewBox="0 0 16 16" aria-hidden="true">
          <path d="M1 5c0-2 3-3 7-3s7 1 7 3v1.5h-3.5V5h-7v1.5H1z"/>
          <path d="M4 7h8l2 7H2z"/>
        </svg>
        <span>+1 555 308 4726</span>
      </li>
      <li class="contact__item">
        <svg class="contact__icon" viewBox="0 0 16 16" aria-hidden="true">
          <path d="M1 3h14v10H1z M2.2 4.2 8 8.6l5.8-4.4z" fill-rule="evenodd"/>
        </svg>
        <span>Dale@prairielanternpopcorn.com</span>
      </li>
    </ul>

    <div class="web-band">www.prairielanternpopcorn.com</div>
  </section>

</main>
</body>
</html>
```